Album Cover Art for New Single

Independent singer-songwriter and pianist, seeking design work for a new single "Walk Beside the Lantern". Christian & Gospel music format. See attached for master recording.

This single is personal for me, so I'm looking for an image that really captures the heart of the message. Redemption, forgiveness, prodigals returning home to a loving father.
Updates

Target Market(s)

Millenials

Colors

Designer to choose colors to be used in the design.

Requirements
Must have
• simple graphic, must include the following text:
• Walk Beside the Lantern
• Dale Verrick
Should not have
• Avoid "cheesy" look and feel.

```html
<!DOCTYPE html>
<html lang="en">
<head>
<meta charset="utf-8">
<title>Walk Beside the Lantern — Dale Verrick</title>
<link rel="stylesheet" href="https://fonts.googleapis.com/css2?family=Cinzel:wght@500&family=Open+Sans:wght@300&display=swap">
<style>
  :root {
    --paper: #ffffff;
    --ink: #111111;
    --title-light: #ffffff;
    --sky: #d3d6d7;
    --mist: #b9bcbd;
    --rock: #7c7b7a;
    --forest: #3a3735;
    --valley: #1f1d1c;
  }
  html, body {
    margin: 0;
    padding: 0;
    overflow: hidden;
    background: var(--paper);
  }
  .cover {
    position: relative;
    width: 1200px;
    height: 1200px;
    overflow: hidden;
    background: var(--paper);
  }
  .cover__landscape {
    position: absolute;
    left: 0;
    top: 230px;
    width: 1200px;
    height: 970px;
    display: block;
  }
  .cover__title {
    position: absolute;
    left: 86px;
    top: 54px;
    margin: 0;
    font-family: "Open Sans", "Helvetica Neue", Arial, sans-serif;
    font-weight: 300;
    font-size: 188px;
    line-height: 163px;
    letter-spacing: -0.01em;
    text-transform: uppercase;
  }
  .cover__title-line {
    display: block;
    color: var(--title-light);
    white-space: nowrap;
  }
  .cover__title-line--lead {
    color: var(--ink);
  }
  .cover__artist {
    position: absolute;
    right: 88px;
    top: 1096px;
    margin: 0;
    font-family: "Cinzel", "Times New Roman", serif;
    font-weight: 500;
    font-size: 34px;
    letter-spacing: 0.3em;
    color: var(--title-light);
    text-transform: uppercase;
    white-space: nowrap;
  }
</style>
</head>
<body>
  <main class="cover">
    <svg class="cover__landscape" viewBox="0 0 1200 970" role="img" aria-label="Misty snow-capped mountain above a fog-filled valley and dark pine forest">
      <defs>
        <linearGradient id="landscape-tone" x1="0" y1="0" x2="0" y2="1">
          <stop offset="0" stop-color="var(--sky)"/>
          <stop offset="0.25" stop-color="var(--mist)"/>
          <stop offset="0.55" stop-color="var(--rock)"/>
          <stop offset="0.8" stop-color="var(--forest)"/>
          <stop offset="1" stop-color="var(--valley)"/>
        </linearGradient>
      </defs>
      <rect width="1200" height="970" fill="url(#landscape-tone)"/>
    </svg>

    <h1 class="cover__title">
      <span class="cover__title-line cover__title-line--lead">Walk</span>
      <span class="cover__title-line">Beside</span>
      <span class="cover__title-line">The</span>
      <span class="cover__title-line">Lantern</span>
    </h1>

    <p class="cover__artist">Dale Verrick</p>
  </main>
</body>
</html>
```